Make attractive Packaging label for NUT BUTTERS jars

We at Velora Pantry are launching our own line of NUT BUTTERS. We will be serving them in GLASS JARS ready packaged. I need attractive luxurious design for glass jar and should be designed ready to print.
I have attached glass jar pictures and measurement sheet.
My company logo has been attached. Also company details can be found on our facebook page.
product will be

ALMOND BUTTER
CASHEW BUTTER
PEANUT BUTTER
HAZELNUT BUTTER.

Industry/Entity Type

Retail

```html
<!DOCTYPE html>
<html lang="en">
<head>
<meta charset="utf-8">
<title>Velora Pantry – Cashew Butter Jar Label</title>
<link rel="stylesheet" href="https://fonts.googleapis.com/css2?family=Open+Sans:wght@400;600;800&family=Kalam:wght@700&display=swap">
<style>
  :root {
    --page: #ffffff;
    --cream: #fbf8ef;
    --lime: #84fc0a;
    --lime-pale: #d9f7a0;
    --cocoa: #2f1c17;
    --caramel: #b8731f;
    --ink: #1d1d1d;
    --white: #ffffff;
    --badge-orange: #f08a1c;
    --badge-green: #7ccc2c;
  }
  * { margin: 0; padding: 0; box-sizing: border-box; }
  html, body { width: 1200px; height: 1000px; overflow: hidden; background: var(--page); }
  .canvas { position: relative; width: 1200px; height: 1000px; font-family: "Open Sans", Arial, sans-serif; }

  .label { position: absolute; left: 5px; top: 337px; width: 1195px; height: 271px; overflow: hidden; }
  .label-bg { position: absolute; inset: 0; width: 100%; height: 100%; }

  .contact { position: absolute; left: 35px; top: 39px; color: var(--ink); font-size: 13.5px; line-height: 17px; }
  .contact-row { display: flex; align-items: flex-start; gap: 10px; margin-bottom: 6px; }
  .contact-row svg { flex: 0 0 14px; width: 14px; height: 14px; margin-top: 1px; fill: var(--ink); }
  .contact-row p { width: 285px; }

  .brand { position: absolute; left: 438px; top: 20px; width: 280px;
           font-weight: 800; color: var(--caramel); letter-spacing: -1px; }
  .brand-line { display: block; }
  .brand-line--top { font-size: 66px; line-height: 72px; }
  .brand-line--bottom { font-size: 40px; line-height: 42px; margin-left: 22px; }

  .product { position: absolute; left: 565px; top: 135px; width: 200px; height: 135px; }
  .product svg { position: absolute; inset: 0; }
  .product-name { position: absolute; left: 18px; top: 22px; width: 160px; text-align: center;
                  font-family: "Kalam", cursive; color: var(--white); font-size: 46px; line-height: 46px; }
  .product-type { position: absolute; left: 30px; top: 72px; width: 120px; text-align: center;
                  color: var(--white); font-size: 20px; letter-spacing: 2px; transform: rotate(-4deg); }
  .product-art { position: absolute; left: 140px; top: 72px; width: 72px; height: 48px; border-radius: 40% 50% 45% 50%;
                 background: linear-gradient(135deg, #e6b46a, #b87530 60%, #4f8d26); }

  .badges { position: absolute; left: 870px; top: 32px; display: flex; gap: 28px; }
  .badge { width: 66px; height: 66px; border-radius: 50%; border: 3px solid var(--cocoa); }
  .badge--orange { background: var(--badge-orange); }
  .badge--green { background: var(--badge-green); }

  .blurb { position: absolute; left: 840px; top: 163px; width: 322px; color: var(--white);
           font-size: 12.5px; line-height: 17px; text-align: justify; }
</style>
</head>
<body>
<main class="canvas">
  <section class="label">
    <svg class="label-bg" viewBox="0 0 1195 271" preserveAspectRatio="none" aria-hidden="true">
      <rect width="1195" height="271" fill="var(--cream)"/>
      <rect width="1195" height="18" fill="var(--lime)"/>
      <polygon points="0,228 1195,92 1195,271 0,271" fill="var(--lime-pale)"/>
      <polygon points="0,243 1195,108 1195,271 0,271" fill="var(--lime)"/>
    </svg>

    <div class="contact">
      <div class="contact-row">
        <svg viewBox="0 0 14 14"><path d="M7 0a5 5 0 0 1 5 5c0 4-5 9-5 9S2 9 2 5a5 5 0 0 1 5-5zm0 3a2 2 0 1 0 0 4 2 2 0 0 0 0-4z"/></svg>
        <p>Harbour Lane Market, North Quay Street, Corkwell, Ireland</p>
      </div>
      <div class="contact-row">
        <svg viewBox="0 0 14 14"><circle cx="7" cy="7" r="6.2" fill="none" stroke="var(--ink)" stroke-width="1.6"/><path d="M1 7h12M7 1c-3 3-3 9 0 12M7 1c3 3 3 9 0 12" fill="none" stroke="var(--ink)" stroke-width="1.2"/></svg>
        <p>www.velorapantry.ie</p>
      </div>
      <div class="contact-row">
        <svg viewBox="0 0 14 14"><path d="M0 3h14v9H0z"/><path d="M0 3l7 5 7-5" fill="none" stroke="var(--cream)" stroke-width="1.2"/></svg>
        <p>info@velorapantry.ie</p>
      </div>
      <div class="contact-row">
        <svg viewBox="0 0 14 14"><path d="M3 0l2.5 3.5-1.5 1.5c.8 2 2.5 3.7 4.5 4.5L10 8l4 2.5-1.5 3C6 13.5.5 8 .5 1.5z"/></svg>
        <p>353 85 204 7731<br>085 418 6620<br>085 204 7731</p>
      </div>
    </div>

    <h1 class="brand">
      <span class="brand-line brand-line--top">Velora</span>
      <span class="brand-line brand-line--bottom">Pantry</span>
    </h1>

    <div class="product">
      <svg viewBox="0 0 200 135" aria-hidden="true">
        <path d="M30 20C70 -5 170 -10 190 30c15 35-5 80-55 95C80 140 10 125 5 85 2 60 10 35 30 20z" fill="var(--cocoa)"/>
      </svg>
      <p class="product-name">Cashew</p>
      <p class="product-type">BUTTER</p>
      <div class="product-art" role="img" aria-label="Cashew nuts with green leaves"></div>
    </div>

    <div class="badges">
      <div class="badge badge--orange" role="img" aria-label="Gluten free badge"></div>
      <div class="badge badge--green" role="img" aria-label="Vegan badge"></div>
      <div class="badge badge--green" role="img" aria-label="All natural badge"></div>
    </div>

    <p class="blurb">A unique Corkwell's only exquisite edible Nuts, Seed and Dried Fruit shop. From sweet and savoury snacking nuts to raw healthy nuts &amp; seeds and Dried fruits.</p>
  </section>
</main>
</body>
</html>
```